New business stationairy

I need paper with header and footer and business cards.
I am a Ltd Company and my main field of expertise is QA/QC inspection in the Oil and Gas Industry. I will need all contact detail inserted and a footer with registration number and bank details etc

```html
<!DOCTYPE html>
<html lang="en">
<head>
<meta charset="utf-8">
<title>Halden Verification Services Ltd – Business Card</title>
<link rel="stylesheet" href="https://fonts.googleapis.com/css2?family=Orbitron:wght@700&family=Libre+Baskerville:wght@400;700&display=swap">
<style>
  :root {
    --paper: #ffffff;
    --navy: #262c6e;
    --navy-soft: #5a5f9a;
    --rule-fade: #e4e5f0;
    --brand-blue: #1b2fd8;
    --name-blue: #2445f0;
    --ink: #111111;
  }
  html, body {
    margin: 0;
    padding: 0;
    overflow: hidden;
    background: var(--paper);
  }
  .card {
    position: relative;
    width: 1200px;
    height: 690px;
    background: var(--paper);
    overflow: hidden;
    font-family: "Libre Baskerville", Georgia, serif;
    color: var(--ink);
  }
  .card-frame {
    position: absolute;
    inset: 0;
  }
  .corner-mark {
    position: absolute;
    border-radius: 0 60% 60% 0 / 0 50% 50% 0;
    background: linear-gradient(90deg, #3a3a3f 0%, #2b3170 45%, #3b4290 100%);
  }
  .corner-mark--top {
    left: 0;
    top: 0;
    width: 86px;
    height: 169px;
  }
  .corner-mark--bottom {
    right: 0;
    bottom: 0;
    width: 103px;
    height: 193px;
    border-radius: 60% 0 0 60% / 50% 0 0 50%;
    background: linear-gradient(270deg, #3a3a3f 0%, #2b3170 45%, #3b4290 100%);
  }
  .company-name {
    position: absolute;
    left: 110px;
    top: 70px;
    width: 1010px;
    margin: 0;
    text-align: center;
    white-space: nowrap;
    font-family: "Orbitron", "Arial Black", sans-serif;
    font-weight: 700;
    font-size: 40px;
    line-height: 1;
    letter-spacing: 3px;
    color: var(--brand-blue);
  }
  .holder {
    position: absolute;
    left: 171px;
    top: 270px;
    width: 200px;
    text-align: center;
  }
  .holder-name {
    display: block;
    white-space: nowrap;
    margin-left: -100px;
    margin-right: -100px;
    font-weight: 700;
    font-size: 38px;
    line-height: 1.4;
    color: var(--name-blue);
  }
  .holder-role {
    display: block;
    font-weight: 700;
    font-size: 37px;
    line-height: 1.4;
    color: var(--ink);
  }
  .address {
    position: absolute;
    right: 77px;
    top: 202px;
    margin: 0;
    text-align: right;
    font-style: normal;
    font-size: 33px;
    line-height: 43.5px;
  }
  .address span { display: block; }
  .contact {
    position: absolute;
    left: 0;
    top: 571px;
    width: 1194px;
    margin: 0;
    text-align: center;
    font-size: 33px;
    line-height: 43px;
  }
  .contact span { display: block; }
</style>
</head>
<body>
  <main class="card">
    <svg class="card-frame" width="1200" height="690" viewBox="0 0 1200 690" aria-hidden="true">
      <defs>
        <linearGradient id="rule-fade" x1="0" y1="0" x2="1" y2="0">
          <stop offset="0" stop-color="#262c6e"/>
          <stop offset="0.5" stop-color="#e4e5f0"/>
          <stop offset="1" stop-color="#262c6e"/>
        </linearGradient>
      </defs>
      <rect class="rule rule--top" x="69" y="165" width="1068" height="2" fill="url(#rule-fade)"/>
      <rect class="rule rule--bottom" x="40" y="505" width="1114" height="2" fill="url(#rule-fade)"/>
      <rect class="bar bar--right" x="1163" y="6" width="7" height="300" fill="#262c6e"/>
      <rect class="bar bar--left" x="25" y="386" width="7" height="304" fill="#262c6e"/>
    </svg>

    <div class="corner-mark corner-mark--top" role="img" aria-label="Curved blue flame-like decorative swoosh"></div>
    <div class="corner-mark corner-mark--bottom" role="img" aria-label="Curved blue flame-like decorative swoosh"></div>

    <h1 class="company-name">HALDEN VERIFICATION SERVICES LTD</h1>

    <div class="holder">
      <span class="holder-name">Maren Holt</span>
      <span class="holder-role">Director</span>
    </div>

    <address class="address">
      <span>The Willows</span>
      <span>Mill Lane</span>
      <span>Ashcombe</span>
      <span>Fordbridge</span>
      <span>Wessex</span>
      <span>AB12 3CD</span>
    </address>

    <p class="contact">
      <span>Email: mholt@haldenvs.co.uk</span>
      <span>mobile: 07700900123</span>
    </p>
  </main>
</body>
</html>
```